Independent book publisher needs book cover design

We need a full book cover (front, back and spine) designed for one of our authors and a detailed specification doc is attached.

The book is titled, "Steady Hands, Quiet Harbors: A Field Guide to Backup Routes; since drafting a route is gentler than cleaning up the wreckage". It outlines a structured process by which women can avoid or reduce risk and uncertainty in their lives. It is written for women who have a lot to lose.

A good metaphor for this book would be one that is related to prevention or rescue. The author prefers something based on a lifeboat or perhaps an empty life preserver (maybe with sinking ship and sharks in background). Other ideas are welcomed.

Target Market(s)

It is written for women who have a lot to lose.

Industry/Entity Type

Book Publisher

Requirements
Must have
• See attachment.
• Please note:
• The uploaded file has been updated and a bar code file has been uploaded.

```html
<!DOCTYPE html>
<html lang="en">
<head>
<meta charset="utf-8">
<title>Steady Hands, Quiet Harbors — Cover</title>
<link rel="stylesheet" href="https://fonts.googleapis.com/css2?family=Roboto+Condensed:wght@400;700;800&display=swap">
<style>
  :root {
    --backdrop: #4f4f4f;
    --paper: #ffffff;
    --red: #c8161d;
    --red-deep: #9c0f14;
    --ink: #111111;
    --sky-top: #6f8599;
    --sky-mid: #aab5bf;
    --cloud: #d8d8d4;
    --pier: #b5aca0;
  }
  * { box-sizing: border-box; margin: 0; padding: 0; }
  html, body { width: 1200px; height: 999px; overflow: hidden; }
  body {
    background: var(--backdrop);
    font-family: "Roboto Condensed", "Arial Narrow", sans-serif;
    position: relative;
  }
  .book {
    position: absolute;
    left: 322px;
    top: 120px;
    display: flex;
    height: 760px;
  }
  .spine {
    width: 56px;
    height: 100%;
    background: var(--paper);
    border-right: 1px solid #d6d6d6;
    display: flex;
    flex-direction: column;
    align-items: center;
    justify-content: space-between;
    padding: 28px 0 30px;
  }
  .spine-title, .spine-author {
    writing-mode: vertical-rl;
    color: var(--red);
    font-weight: 700;
    white-space: nowrap;
  }
  .spine-title { font-size: 25px; }
  .spine-author { font-size: 22px; }
  .front {
    position: relative;
    width: 500px;
    height: 100%;
    background: var(--paper);
    overflow: hidden;
  }
  .front-art { position: absolute; inset: 0; }
  .title {
    position: absolute;
    left: 40px;
    top: 24px;
    line-height: 1;
    text-transform: uppercase;
    font-weight: 800;
  }
  .title-line { display: block; }
  .title-big { color: var(--red); font-size: 54px; letter-spacing: -0.5px; }
  .title-small { color: var(--ink); font-size: 26px; font-weight: 700; }
  .title-line + .title-line { margin-top: 2px; }
  .title-tag { color: var(--ink); font-size: 20px; font-weight: 700; margin-top: 10px; }
  .subtitle {
    position: absolute;
    left: 0;
    right: 0;
    top: 656px;
    text-align: center;
    color: var(--ink);
    font-weight: 700;
    font-size: 17px;
    line-height: 1.35;
  }
  .author {
    position: absolute;
    left: 0;
    right: 0;
    top: 712px;
    text-align: center;
    color: var(--red);
    font-weight: 700;
    font-size: 23px;
    letter-spacing: 2px;
    text-transform: uppercase;
  }
</style>
</head>
<body>
  <div class="book">
    <div class="spine">
      <span class="spine-title">Steady Hands, Quiet Harbors</span>
      <span class="spine-author">Mira Calloway</span>
    </div>

    <div class="front">
      <svg class="front-art" width="500" height="760" viewBox="0 0 500 760">
        <defs>
          <linearGradient id="sky" x1="0.9" y1="0" x2="0.3" y2="1">
            <stop offset="0" stop-color="var(--sky-top)"/>
            <stop offset="0.4" stop-color="var(--sky-mid)"/>
            <stop offset="0.7" stop-color="var(--cloud)"/>
            <stop offset="1" stop-color="var(--pier)"/>
          </linearGradient>
          <linearGradient id="band" x1="0" y1="0" x2="1" y2="0">
            <stop offset="0" stop-color="var(--red-deep)"/>
            <stop offset="0.5" stop-color="var(--red)"/>
            <stop offset="1" stop-color="var(--red-deep)"/>
          </linearGradient>
        </defs>
        <path class="cover-photo" role="img"
              aria-label="Photo of a small boy holding a briefcase on a wooden pier, facing a cloudy sky dotted with hot air balloons"
              fill="url(#sky)"
              d="M0,318 C170,311 340,275 500,222 L500,560 C340,590 170,605 0,608 Z"/>
        <path class="swoosh-top" fill="url(#band)"
              d="M0,270 C170,260 340,222 500,168 L500,212 C340,264 170,302 0,310 Z"/>
        <path class="swoosh-top-thin" fill="var(--red)"
              d="M0,256 C170,246 340,206 500,150 L500,157 C340,214 170,252 0,262 Z"/>
        <path class="swoosh-bottom" fill="url(#band)"
              d="M0,615 C170,612 340,596 500,568 L500,582 C340,618 170,640 0,648 Z"/>
      </svg>

      <h1 class="title">
        <span class="title-line"><span class="title-big">Steady</span> <span class="title-small">Hands,</span></span>
        <span class="title-line title-big">Quiet Harbors</span>
        <span class="title-line title-tag">A Field Guide to Backup Routes</span>
      </h1>

      <p class="subtitle">since drafting a route is gentler<br>than cleaning up the wreckage</p>
      <p class="author">Mira Calloway</p>
    </div>
  </div>
</body>
</html>
```